Packaging design for a reclosable bag for our product

We have a logo, and we need to put it on packaging for our product and while we want the look to be simple, we want it to follow good design principles and also contain spaces for other product descriptions.

There will be 5 sizes at launch so I'd like 5 variations, one for each size.

I've included a few mockups of the type of bag that I made but they are all just rough ideas that I had.

I want the brand to look scientific and methodical and even a bit quirky, as in "wow this is a serious product but also a bit unusual."

```html
<!DOCTYPE html>
<html lang="en">
<head>
<meta charset="utf-8">
<title>QV7 Bias Lighting – Extra Large 5m Pouch</title>
<link rel="stylesheet" href="https://fonts.googleapis.com/css2?family=Archivo:wght@800&family=Roboto+Condensed:wght@700&family=Roboto+Slab:wght@400&display=swap">
<style>
  :root {
    --backdrop: #d3d3d3;
    --pouch-light: #e2e2e2;
    --pouch-dark: #0b0b0b;
    --zip-line: #262626;
    --ink: #111111;
    --paper: #f2f2f2;
  }
  * { margin: 0; padding: 0; box-sizing: border-box; }
  html, body { width: 1200px; height: 848px; overflow: hidden; }
  body { background: var(--backdrop); position: relative; font-family: "Roboto Condensed", sans-serif; }

  .pouch {
    position: absolute;
    left: 405px; top: 191px;
    width: 340px; height: 483px;
    background: var(--pouch-light);
    border-radius: 2px 2px 6px 6px;
    overflow: hidden;
  }
  .pouch__band {
    position: absolute; left: 0; top: 0;
    width: 100%; height: 183px;
    background: var(--pouch-dark);
  }
  .pouch__zip {
    position: absolute; left: 0; top: 38px;
    width: 100%; height: 1px;
    background: var(--zip-line);
  }

  /* positions below are relative to the canvas */
  .brand-name {
    position: absolute; left: 465px; top: 262px;
    width: 217px;
    font-family: "Archivo", sans-serif; font-weight: 800;
    font-size: 96px; line-height: 1; letter-spacing: -2px;
    text-align: center;
    color: var(--paper);
  }
  .product-line {
    position: absolute; left: 467px; top: 432px;
    width: 215px; height: 27px;
    background: var(--ink);
    font-family: "Roboto Slab", serif; font-weight: 400;
    font-size: 22px; line-height: 28px; letter-spacing: 0.3px;
    color: var(--paper);
    text-align: center;
    white-space: nowrap;
  }
  .size-number {
    position: absolute; left: 465px; top: 448px;
    font-family: "Roboto Condensed", sans-serif; font-weight: 700;
    font-size: 257px; line-height: 1;
    color: var(--ink);
    transform: scaleX(0.74);
    transform-origin: left top;
  }
  .rule {
    position: absolute; left: 569px;
    width: 110px; height: 1px;
    background: var(--ink);
  }
  .rule--top { top: 481px; }
  .rule--mid { top: 510px; }
  .rule--low { top: 610px; }
  .size-label {
    position: absolute; left: 569px; top: 487px;
    width: 110px;
    font-weight: 700; font-size: 19px; line-height: 1;
    color: var(--ink); white-space: nowrap;
  }
  .size-unit {
    position: absolute; left: 567px; top: 503px;
    font-weight: 700; font-size: 112px; line-height: 1;
    color: var(--ink);
  }
  .spec {
    position: absolute; left: 566px; top: 622px;
    font-family: "Roboto Slab", serif; font-size: 10px; line-height: 13px;
    color: var(--ink); white-space: nowrap;
  }
</style>
</head>
<body>
  <div class="pouch">
    <div class="pouch__band"></div>
    <div class="pouch__zip"></div>
  </div>

  <div class="brand-name">QV7</div>
  <div class="product-line">BIAS LIGHTING</div>

  <div class="size-number">5</div>

  <div class="rule rule--top"></div>
  <div class="size-label">EXTRA LARGE</div>
  <div class="rule rule--mid"></div>
  <div class="size-unit">m</div>
  <div class="rule rule--low"></div>
  <p class="spec">6500K White Bias Lighting<br>Simulated D65 CRI 90+</p>
</body>
</html>
```